Business Card Design for Varomir Facility Services

We are looking for a Business Card Design for the Company "Varomir Facility Services."
Front side:
- Company Logo (small)
- Company Name, address, pohone, website and personal data.
- white background, for text e.g. company colors (blue or green like in the logo)
Please use following data:
Company data:
Varomir Facility Services Kostelac
Birkenhaldweg 14
6347 Rindenau
www.varomir-fs.ch
Person data:
Tarik Kostelac
Geschäftsführer
+41 76 519 47 83
info@varomir-fs.ch
Back side:
could be colored in blue or green
please use a big logo sing and some smaller icons to say what is all beeing offered in facility services, like cleaning, maintenance cleaning
industrial cleaning, caretaking, gardening, disposal. There is no need for everyone of the icons if there are similar or an icon is standing for more of them.
colors to use:
blue: HEX 246BB0
green: HEX 52B33E

```html
<!DOCTYPE html>
<html lang="de">
<head>
<meta charset="utf-8">
<title>Varomir Facility Services – Business Card</title>
<link href="https://fonts.googleapis.com/css2?family=Lato:wght@400;700&display=swap" rel="stylesheet">
<style>
  :root {
    --brand-blue: #236bb1;
    --brand-green: #7fbe28;
    --paper: #ffffff;
    --ink: #1f1f1f;
    --rule: #c9c9c9;
    --backdrop: #b9b9b9;
  }
  * { margin: 0; padding: 0; box-sizing: border-box; }
  html, body { width: 1200px; height: 802px; overflow: hidden; }
  body {
    background: var(--backdrop);
    font-family: "Lato", sans-serif;
    position: relative;
  }
  .card {
    position: absolute;
    top: 274px;
    width: 443px;
    height: 265px;
    overflow: hidden;
    box-shadow: 0 3px 8px rgba(0,0,0,0.35);
  }
  .card-front { left: 136px; background: var(--brand-blue); color: var(--paper); }
  .card-back { left: 624px; background: var(--paper); color: var(--ink); }

  .front-decoration {
    position: absolute;
    left: 0; top: 0;
    width: 443px; height: 265px;
  }
  .person { position: absolute; left: 24px; top: 39px; }
  .person-name { font-size: 16.5px; font-weight: 700; letter-spacing: 0.2px; line-height: 1; }
  .person-role { font-size: 12.5px; line-height: 1.15; margin-top: 1px; }

  .contact { position: absolute; left: 24px; top: 92px; list-style: none; }
  .contact li { font-size: 12.5px; line-height: 16px; display: flex; align-items: center; gap: 5px; }
  .contact svg { width: 9px; height: 9px; fill: var(--paper); }

  .company {
    position: absolute; left: 24px; top: 163px;
    font-size: 12.5px; line-height: 15.8px; font-style: normal;
  }

  .brand {
    position: absolute;
    left: 0; right: 0; top: 104px;
    display: flex; justify-content: center; align-items: center; gap: 9px;
  }
  .brand-dot { width: 16px; height: 16px; border-radius: 50%; background: var(--brand-green); }
  .brand-name { font-size: 22px; font-weight: 700; color: var(--brand-blue); letter-spacing: 0.6px; }

  .divider {
    position: absolute; left: 44px; right: 48px; top: 195px;
    height: 1px; background: var(--rule);
  }
  .service-icon {
    position: absolute; left: 200px; top: 177px;
    width: 36px; height: 36px; border-radius: 50%;
    background: var(--brand-blue);
    display: flex; align-items: center; justify-content: center;
  }
  .service-icon svg { width: 22px; height: 22px; }
  .services {
    position: absolute; left: 0; right: 0; top: 215px;
    text-align: center; font-size: 11.6px; line-height: 14px;
    text-transform: uppercase; letter-spacing: 0.1px;
  }
</style>
</head>
<body>

<section class="card card-front" aria-label="Vorderseite">
  <svg class="front-decoration" viewBox="0 0 443 265" aria-hidden="true">
    <path d="M265 0 C200 60 165 130 200 190 C225 235 300 262 443 265 L443 0 Z" fill="var(--paper)"/>
    <path d="M330 25 C250 70 215 140 250 195 C275 230 340 250 443 252 L443 0 L370 0 Z" fill="var(--brand-green)"/>
  </svg>

  <div class="person">
    <p class="person-name">TARIK KOSTELAC</p>
    <p class="person-role">Geschäftsführer</p>
  </div>

  <ul class="contact">
    <li><svg viewBox="0 0 10 10"><path d="M1 3c0-1 1-2 4-2s4 1 4 2v1H7V3H3v1H1zM2 5h6l1 4H1z"/></svg>+41 76 519 47 83</li>
    <li><svg viewBox="0 0 10 10"><path d="M0 2h10v6H0zM1 3v.5l4 2.5 4-2.5V3L5 5.5z" fill-rule="evenodd"/></svg>info@varomir-fs.ch</li>
    <li><svg viewBox="0 0 10 10"><circle cx="5" cy="5" r="4.5"/></svg>www.varomir-fs.ch</li>
  </ul>

  <address class="company">
    Varomir Facility Services<br>
    Kostelac<br>
    Birkenhaldweg 14<br>
    6347 Rindenau
  </address>
</section>

<section class="card card-back" aria-label="Rückseite">
  <div class="brand">
    <span class="brand-dot"></span>
    <span class="brand-name">Varomir Facility Services</span>
  </div>

  <div class="divider"></div>
  <div class="service-icon">
    <svg viewBox="0 0 22 22" aria-hidden="true">
      <line x1="17" y1="3" x2="11" y2="11" stroke="#fff" stroke-width="2" stroke-linecap="round"/>
      <path d="M9 10l5 4-4 6-7-5z" fill="#fff"/>
    </svg>
  </div>

  <p class="services">
    Cleaning | Maintenance Cleaning | Industrial Cleaning<br>
    Caretaking | Gardening | Disposal
  </p>
</section>

</body>
</html>
```